Website for my photography business

I need a website for my photography business, Bram Kellet Photography. I need a website that has a landing page with a cover photo of each kind of photography I do. For example, Nature, Weddings, Portraits and Architecture. I want it so that when someone comes onto my website they have to choose which kind of photography page they want to visit. So if they click on the wedding photo it will open to a page with my wedding portfolio images and a contact me button. If they choose nature photography I want them to be redirected to an e-commerce section where they can purchase prints. Architecture and Portraits should open up to their respective portfolios with about me and contact info. I like this kind of format because I want people who come to my website for a specific type of photography to be able to be directed there easily without having to look at a mix of other kinds of photography. I will provide a few files to use as placeholders. I have already purchased the bramkelletphotography.example domain name. A Wix website would be great because I am most familiar with it but I am open to anything.

Industry/Entity Type

Photographer

Number of Pages Required

5+ page

Requirements
Must have
• Landing Page and e-commerce

```html
<!DOCTYPE html>
<html lang="en">
<head>
<meta charset="utf-8">
<title>Weddings | Bram Kellet Photography</title>
<link rel="stylesheet" href="https://fonts.googleapis.com/css2?family=Josefin+Sans:wght@300;400&family=Mrs+Saint+Delafield&display=swap">
<style>
  :root {
    --navy: #0a0e21;
    --white: #ffffff;
    --ink: #1d1f2e;
    --badge: #e5141b;
    --muted: #3a3c48;
  }
  * { box-sizing: border-box; margin: 0; padding: 0; }
  html, body { width: 1200px; height: 1196px; overflow: hidden; background: var(--white); }
  body { font-family: "Josefin Sans", sans-serif; color: var(--white); }

  .site-header { position: relative; height: 359px; background: var(--navy); }
  .brand { position: absolute; left: 82px; top: 58px; display: flex; align-items: center; gap: 10px;
    font-family: "Josefin Sans", sans-serif; font-weight: 300; font-size: 19px; color: var(--white); letter-spacing: 0.5px; }
  .brand-dot { width: 8px; height: 8px; border-radius: 50%; background: var(--white); }
  .main-nav { position: absolute; top: 68px; left: 573px; display: flex; gap: 0; }
  .main-nav a { color: var(--white); text-decoration: none; font-weight: 300; font-size: 20px; letter-spacing: 1.6px; }
  .nav-portfolio { position: absolute; left: 0; }
  .nav-about { position: absolute; left: 154px; }
  .nav-contact { position: absolute; left: 268px; }
  .nav-shop { position: absolute; left: 410px; }
  .cart { position: absolute; left: 1078px; top: 64px; width: 28px; height: 26px; }
  .cart-badge { position: absolute; left: 1098px; top: 56px; width: 18px; height: 18px; border-radius: 50%;
    background: var(--badge); color: var(--white); font-size: 10px; line-height: 19px; text-align: center; font-family: Arial, sans-serif; }
  .page-title { position: absolute; top: 150px; left: 0; width: 1200px; text-align: center;
    font-family: "Mrs Saint Delafield", cursive; font-size: 150px; font-weight: 400; line-height: 1;
    text-shadow: 2px 3px 4px rgba(0,0,0,0.6); }

  .gallery { position: relative; height: 597px; overflow: hidden; }
  .slide-prev { position: absolute; left: 0; top: 0; width: 181px; height: 597px;
    background: radial-gradient(circle at 40% 30%, #3f4a3a, #1c2419 55%, #0d120d); }
  .slide-next { position: absolute; left: 1051px; top: 0; width: 149px; height: 597px;
    background: linear-gradient(180deg, #c9ccc6 0%, #a9b989 25%, #8aa565 55%, #6f9a48 80%, #5d8c3b 100%); }
  .slide-current { position: absolute; left: 181px; top: 0; width: 870px; height: 597px;
    background: radial-gradient(ellipse at 50% 60%, #8c7d6c, #a6917a 40%, #b7a58f 65%, #6e6a70 100%); }
  .slide-caption { position: absolute; left: 0; bottom: 0; width: 100%; height: 160px;
    background: linear-gradient(180deg, rgba(10,14,33,0) 0%, rgba(10,14,33,0.75) 100%); }
  .slide-title { position: absolute; left: 52px; top: 526px; font-weight: 300; font-size: 36px; letter-spacing: 9px; }
  .see-more { position: absolute; left: 624px; top: 518px; width: 195px; height: 45px; border: 2px solid var(--white);
    border-radius: 23px; color: var(--white); text-decoration: none; font-weight: 300; font-size: 19px;
    letter-spacing: 4px; line-height: 45px; text-align: center; }
  .arrow { position: absolute; top: 278px; width: 24px; height: 44px; }
  .arrow-prev { left: 110px; }
  .arrow-next { left: 1098px; }

  .site-footer { position: relative; height: 240px; background: var(--white); }
  .social { position: absolute; top: 52px; left: 0; width: 1200px; display: flex; justify-content: center; gap: 30px; }
  .social a { color: var(--ink); text-decoration: none; font-size: 15px; font-weight: 400; letter-spacing: 1px; }
  .copyright { position: absolute; top: 160px; left: 0; width: 1200px; text-align: center; color: var(--muted);
    font-size: 13px; letter-spacing: 4.3px; font-weight: 400; }
</style>
</head>
<body>
  <header class="site-header">
    <div class="brand"><span class="brand-dot"></span>Bram Kellet Photography</div>
    <nav class="main-nav">
      <a class="nav-portfolio" href="#">PORTFOLIO</a>
      <a class="nav-about" href="#">ABOUT</a>
      <a class="nav-contact" href="#">CONTACT</a>
      <a class="nav-shop" href="#">SHOP</a>
    </nav>
    <svg class="cart" viewBox="0 0 28 26" fill="none" stroke="#fff" stroke-width="2.4" stroke-linecap="round" stroke-linejoin="round" aria-label="Cart">
      <path d="M1 2h4l3 14h15l3-10H7"/>
      <circle cx="10" cy="22" r="2"/><circle cx="21" cy="22" r="2"/>
    </svg>
    <span class="cart-badge">1</span>
    <h1 class="page-title">Weddings</h1>
  </header>

  <section class="gallery">
    <div class="slide-prev" role="img" aria-label="Wedding photo of pine branches with snow"></div>
    <div class="slide-current" role="img" aria-label="Wedding rings resting on a granite rock">
      <div class="slide-caption"></div>
      <h2 class="slide-title">WEDDING 1</h2>
      <a class="see-more" href="#">SEE MORE</a>
    </div>
    <div class="slide-next" role="img" aria-label="Wedding venue with spring trees and lawn"></div>
    <svg class="arrow arrow-prev" viewBox="0 0 24 44" fill="none" stroke="rgba(255,255,255,0.6)" stroke-width="2.5"><path d="M22 2L2 22l20 20"/></svg>
    <svg class="arrow arrow-next" viewBox="0 0 24 44" fill="none" stroke="rgba(255,255,255,0.6)" stroke-width="2.5"><path d="M2 2l20 20L2 42"/></svg>
  </section>

  <footer class="site-footer">
    <div class="social">
      <a href="#">Photofeed</a>
      <a href="#">Friendbook</a>
    </div>
    <p class="copyright">COPYRIGHT BRAM KELLET PHOTOGRAPHY 2020</p>
  </footer>
</body>
</html>
```